Stationery Set for Velmora Company

I need to create full stationery design for my company; Business Cards, Envelops, Letter Heads, Calendar.
In the letter head and Envelops... only contact information and website links.
Our company is a Service Management company with different domains of innovative services including Technology Service Management, Education Services, Outsourcing Management, Events Management.
I need a modern and innovative design specially for the business card. I some transparent designs and I like it, but don't limit your innovation to what I mentioned. Sky is limit for your innovation.

Target Market(s)

Middle East & Africa

Industry/Entity Type

Business Management

Colors
34a7d8
0355a3
85acd3
86cae7
cee9f5
cfdeed
e4daeb
f3f1f8
ecf7fb

Requirements
Must have
• Name, Title, Email, Mobile
Nice to have
• We have multiple locations in USA, KSA, EGY, so I need ideas about how to include all contact details maybe QR / Barcode or something else.
• Please see our locations and contact information: www.brightvelmora.example
Should not have
• Too much text

```html
<!DOCTYPE html>
<html lang="en">
<head>
<meta charset="utf-8">
<title>Velmora Company Stationery</title>
<link href="https://fonts.googleapis.com/css2?family=Arimo:wght@400;700&display=swap" rel="stylesheet">
<style>
:root{
  --bg:#ececec;
  --paper:#ffffff;
  --ink:#3a3a3a;
  --muted:#6b6b6b;
  --brand:#0355a3;
  --sky:#34a7d8;
  --flap-a:#3a3fae;
  --flap-b:#1f8fd6;
  --sig:#cfcfcf;
}
*{margin:0;padding:0;box-sizing:border-box}
html,body{width:1200px;height:937px;overflow:hidden;background:var(--bg)}
body{position:relative;font-family:"Arimo",Arial,sans-serif;color:var(--ink)}
.sheet{position:absolute;background:var(--paper)}
.brand{font-weight:700;color:var(--brand);white-space:nowrap;display:flex;align-items:center;gap:4px;line-height:1}
.brand-dot{display:inline-block;border-radius:50%;background:var(--brand)}

/* letterhead */
.letterhead{left:185px;top:68px;width:388px;height:544px}
.letterhead .brand{position:absolute;left:20px;top:28px;font-size:12px}
.letterhead .brand-dot{width:8px;height:8px}
.lh-contact{position:absolute;right:20px;top:22px;text-align:right;font-size:5px;line-height:7px;color:var(--muted)}
.letter{position:absolute;left:36px;top:139px;width:296px;font-size:5px;line-height:7px;color:var(--ink)}
.letter p{margin-bottom:9px}
.letter .gap{margin-bottom:20px}
.letter strong{font-weight:700}
.signature{width:40px;height:16px;background:var(--sig);margin:4px 0 6px}

/* cover */
.cover{left:636px;top:41px;width:460px;height:575px}
.cover .brand{position:absolute;left:0;right:0;top:262px;justify-content:center;font-size:26px;gap:8px}
.cover .brand-dot{width:14px;height:14px}

/* business cards */
.card-front{left:46px;top:659px;width:176px;height:99px}
.card-front .brand{position:absolute;left:7px;top:13px;font-size:8px}
.card-front .brand-dot{width:5px;height:5px}
.holder{position:absolute;right:8px;top:48px;text-align:right}
.holder .name{font-size:6px;font-weight:700;color:var(--ink)}
.holder .title{font-size:5px;color:var(--muted);margin-top:2px}
.card-contact{position:absolute;left:7px;top:79px;font-size:3.6px;line-height:5px;color:var(--muted)}
.card-contact svg{width:4px;height:4px;vertical-align:middle;margin-right:2px}
.card-web{position:absolute;right:8px;bottom:8px;font-size:4px;letter-spacing:1px;color:var(--muted)}
.card-back{left:46px;top:785px;width:176px;height:99px}
.card-back .brand{position:absolute;left:0;right:0;top:44px;justify-content:center;font-size:9px}
.card-back .brand-dot{width:6px;height:6px}

/* envelopes */
.env-front{left:265px;top:672px;width:433px;height:208px}
.env-front .brand{position:absolute;left:16px;top:28px;font-size:11px}
.env-front .brand-dot{width:7px;height:7px}
.env-back{left:737px;top:672px;width:432px;height:208px}
.env-back svg.flap{position:absolute;left:0;top:0;width:432px;height:72px}
.flap-web{position:absolute;left:0;right:0;top:28px;text-align:center;font-size:10px;letter-spacing:3px;color:#e8f4fb}
</style>
</head>
<body>

<section class="sheet letterhead">
  <div class="brand"><span class="brand-dot"></span>Velmora Company</div>
  <div class="lh-contact">
    2200 Linden Park Ave<br>
    Austin TX 78701<br>
    512.555.0147<br>
    nadia@brightvelmora.example
  </div>
  <div class="letter">
    <p>July 2, 2012</p>
    <p><strong>Dear CH,</strong><br>ABC Building, def St., Country Name</p>
    <p>Thank you for your recent inquiry about our service programs. We are pleased to share an overview of our technology, education, outsourcing and events teams, each ready to support your goals across the region. Our staff will follow up shortly with a tailored proposal, timelines and a clear summary of costs for your review.</p>
    <p class="gap">Please let us know a convenient time to meet so we can discuss your needs in more detail.</p>
    <p>We value the trust you place in our team and look forward to a lasting partnership. Should you have any questions before then, our offices in each location are happy to help, and our coordinators can arrange visits, calls or workshops at a time that suits your schedule best.</p>
    <p>Best Regards,</p>
    <div class="signature" role="img" aria-label="Handwritten signature"></div>
    <p><strong>Omar Haddad</strong><br>Director<br><br>ABC Building, def St., Country Name</p>
  </div>
</section>

<section class="sheet cover">
  <div class="brand"><span class="brand-dot"></span>Velmora Company</div>
</section>

<section class="sheet card-front">
  <div class="brand"><span class="brand-dot"></span>Velmora Company</div>
  <div class="holder">
    <div class="name">Nadia Farrow</div>
    <div class="title">Owner</div>
  </div>
  <div class="card-contact">
    <div><svg viewBox="0 0 10 10"><path d="M2 1h2l1 2-1.2 1a5 5 0 0 0 2.2 2.2L7 5l2 1v2c0 .6-.4 1-1 1A8 8 0 0 1 1 2c0-.6.4-1 1-1z" fill="#6b6b6b"/></svg>512.555.0147</div>
    <div><svg viewBox="0 0 10 10"><rect x="1" y="2" width="8" height="6" fill="#6b6b6b"/></svg>nadia@brightvelmora.example</div>
    <div><svg viewBox="0 0 10 10"><path d="M5 1a3 3 0 0 1 3 3c0 2-3 5-3 5S2 6 2 4a3 3 0 0 1 3-3z" fill="#6b6b6b"/></svg>2200 Linden Park Ave Austin TX 78701</div>
  </div>
  <div class="card-web">www.brightvelmora.example</div>
</section>

<section class="sheet card-back">
  <div class="brand"><span class="brand-dot"></span>Velmora Company</div>
</section>

<section class="sheet env-front">
  <div class="brand"><span class="brand-dot"></span>Velmora Company</div>
</section>

<section class="sheet env-back">
  <svg class="flap" viewBox="0 0 432 72" aria-hidden="true">
    <defs>
      <linearGradient id="flapFill" x1="0" y1="0" x2="1" y2="0">
        <stop offset="0" stop-color="#3a3fae"/>
        <stop offset="0.5" stop-color="#1f9be0"/>
        <stop offset="1" stop-color="#3a3fae"/>
      </linearGradient>
    </defs>
    <path d="M0 0H432V38Q432 72 398 72H34Q0 72 0 38Z" fill="url(#flapFill)"/>
  </svg>
  <div class="flap-web">www.brightvelmora.example</div>
</section>

</body>
</html>
```